Talon Microsystems PowerPoint Master Slide Deck Design

This is a 2-phase project to design a slide deck for a semiconductor company in the Silicon Valley. The design budget will be increased with each phase.
The slide deck will need to have one version with a dark background for presentations and a second version with a white background. Otherwise, the slides will be the same. I anticipate we will need a total of 10 slides, but that number may change.
The first phase will be to design a Title and a Title and Content slide.
- The Title Slide is the first slide of the deck. It should include the presentation title, the presenter's name and date of presentation
- The Title and Content slide should include a title and content with bullet points and up to 2 additional sub-bullets
- The Title and Content slide should have a footer that includes the slide #, Talon Microsystems Confidential, and the logo. This footer will be on every slide except the Title Slide
The first two slides will serve as the format for the remaining ~8 slides:
-Header and Content Text (1, 2, 4 column)
-Header and Content Image (bar chart, pie chart, tables)
-Break
-Title only
-Closing (Talon logo only)
Our slides contain a lot of content so a clean and simple design is best.
Both phases will need to include pre-set color options for
-Text and Lines
-Shadows
-Bullets and sub-bullets (including shapes, ex. circle, slash, square, etc.)
-Bar charts, pie charts, tables
Samples of our collateral are attached. Logo files are also attached
Look and feel
Each slider illustrates characteristics of the customer's brand and the style your logo design should communicate.

```html
<!DOCTYPE html>
<html lang="en">
<head>
<meta charset="utf-8">
<title>Talon Microsystems — Master Slide Deck</title>
<link rel="stylesheet" href="https://fonts.googleapis.com/css2?family=Montserrat:wght@400;500;600;700;800&display=swap">
<style>
  :root {
    --page: #000000;
    --slide: #1f1f20;
    --slide-deep: #19191a;
    --white: #ffffff;
    --cyan: #6cc8e8;
    --blue: #1439ff;
    --blue-mid: #0a63ff;
    --rule: #5a5a5c;
    --box-line: #2f6f8f;
    --muted: #d8d8d8;
  }
  * { margin: 0; padding: 0; box-sizing: border-box; }
  html, body { width: 875px; height: 1200px; overflow: hidden; background: var(--page); }
  body { position: relative; font-family: "Montserrat", sans-serif; color: var(--white); }

  .slide { position: absolute; width: 386px; height: 217px; background: radial-gradient(circle at 50% 45%, #262627 0%, var(--slide) 55%, var(--slide-deep) 100%); overflow: hidden; }
  .col-a { left: 47px; } .col-b { left: 443px; }
  .row-1 { top: 38px; } .row-2 { top: 265px; } .row-3 { top: 492px; } .row-4 { top: 719px; } .row-5 { top: 946px; }

  .top-band { position: absolute; left: 0; top: 0; width: 100%; height: 3px; background: linear-gradient(90deg, var(--blue), var(--blue-mid) 55%, #3fd3f2); }
  .top-band.reverse { background: linear-gradient(90deg, #3fd3f2, var(--blue-mid) 45%, var(--blue)); }

  .footer { position: absolute; left: 0; right: 0; bottom: 0; height: 26px; }
  .footer .rule { position: absolute; left: 34px; right: 34px; top: 0; height: 1px; background: var(--rule); }
  .footer .corner { position: absolute; top: 2px; width: 32px; height: 12px; border-top: 1px solid #777; border-bottom: 1px solid #777; }
  .footer .corner.left { left: 0; } .footer .corner.right { right: 0; }
  .footer-brand { position: absolute; left: 52px; top: 10px; display: flex; align-items: center; gap: 3px; font-size: 5px; font-weight: 700; letter-spacing: .2px; }
  .brand-dot { width: 5px; height: 5px; border: 1px solid var(--white); border-radius: 50%; }
  .copyright { position: absolute; left: 127px; top: 11px; font-size: 5px; letter-spacing: .8px; color: var(--muted); }
  .slide-num { position: absolute; left: 316px; top: 11px; font-size: 5px; font-weight: 700; letter-spacing: .8px; }

  .title-tick { position: absolute; width: 37px; height: 1.5px; background: var(--white); }
  .slide-title { position: absolute; font-size: 19px; font-weight: 700; letter-spacing: 1.3px; white-space: nowrap; }
  .accent { color: var(--cyan); }

  /* Title slide */
  .cover-rule { position: absolute; left: 69px; top: 47px; width: 2px; height: 123px; background: var(--white); }
  .cover-brand { position: absolute; left: 84px; top: 54px; display: flex; align-items: center; gap: 5px; font-size: 11px; font-weight: 600; }
  .cover-brand .brand-dot { width: 10px; height: 10px; border-width: 2px; }
  .cover-title { position: absolute; left: 85px; top: 91px; font-size: 24px; font-weight: 800; line-height: 29px; letter-spacing: .3px; }
  .cover-meta { position: absolute; left: 85px; top: 162px; display: flex; align-items: center; font-size: 7px; font-weight: 600; letter-spacing: 1.6px; }
  .cover-meta .divider { width: 1px; height: 15px; background: var(--white); margin: 0 15px; }

  /* Four-box slide */
  .info-box { position: absolute; width: 167px; height: 48px; border: 1px solid var(--box-line); }
  .info-box .num { position: absolute; left: 8px; top: 11px; font-size: 24px; font-weight: 700; color: var(--cyan); }
  .info-box h3 { position: absolute; left: 49px; top: 6px; font-size: 7px; font-weight: 600; color: var(--cyan); }
  .info-box p { position: absolute; left: 49px; top: 16px; width: 112px; font-size: 3.4px; line-height: 4px; }
  .info-box ul { position: absolute; left: 53px; top: 28px; list-style: none; font-size: 3.2px; line-height: 8px; }

  .bullet::before { content: ""; display: inline-block; width: 5px; height: 1px; background: var(--cyan); vertical-align: middle; margin-right: 1px; }
  .bullet::after { content: ""; position: absolute; }
  .bullet .knob { display: inline-block; width: 3px; height: 3px; border: .8px solid var(--cyan); border-radius: 50%; vertical-align: middle; margin-right: 4px; }

  /* Two-row slide */
  .row-num { position: absolute; font-size: 21px; font-weight: 700; color: var(--cyan); }
  .row-lead { position: absolute; left: 87px; width: 250px; font-size: 7px; line-height: 9px; }
  .row-list { position: absolute; left: 113px; list-style: none; font-size: 6.5px; line-height: 12.5px; }
  .row-divider { position: absolute; left: 34px; width: 322px; height: 1px; background: var(--box-line); }

  /* Two-column slide */
  .col-num { position: absolute; top: 78px; font-size: 21px; font-weight: 700; color: var(--cyan); }
  .col-lead { position: absolute; top: 78px; width: 118px; font-size: 7px; line-height: 8.7px; }
  .col-list { position: absolute; top: 124px; width: 120px; list-style: none; font-size: 6.3px; line-height: 7.5px; }
  .col-list li { margin-bottom: 10px; display: flex; }
  .col-divider { position: absolute; left: 195px; top: 76px; width: 1px; height: 104px; background: var(--rule); }

  /* Four-column slide */
  .quad { position: absolute; top: 68px; width: 80px; }
  .quad .head { display: flex; align-items: center; gap: 7px; }
  .quad .num { font-size: 20px; font-weight: 700; color: var(--cyan); }
  .quad h4 { margin-top: 3px; font-size: 6.6px; font-weight: 600; color: var(--cyan); letter-spacing: .2px; }
  .quad p { margin-top: 12px; font-size: 4.7px; line-height: 5.6px; }
  .quad ul { margin-top: 6px; list-style: none; font-size: 3.3px; line-height: 4px; padding-left: 3px; }
  .quad li { display: flex; margin-bottom: 7px; }
  .quad-divider { position: absolute; top: 74px; width: 1px; height: 85px; background: var(--box-line); }

  /* Image slide */
  .image-well { position: absolute; left: 197px; top: 3px; width: 189px; height: 189px; background: radial-gradient(circle at 60% 55%, #7ed6f7 0%, #2a8ff0 35%, #1044c9 75%, #0b2c8a 100%); }
  .image-well span { position: absolute; left: 50px; top: 80px; font-size: 11px; font-weight: 700; line-height: 15px; letter-spacing: .8px; }
  .side-title { position: absolute; left: 40px; top: 66px; font-size: 20px; font-weight: 700; line-height: 24px; letter-spacing: 1.2px; }

  /* Chart slide */
  .chart-caption { position: absolute; left: 0; width: 100%; top: 69px; text-align: center; font-size: 6.5px; }

  /* Title-only & closing */
  .center-title { position: absolute; left: 0; width: 100%; top: 92px; text-align: center; font-size: 23px; font-weight: 700; letter-spacing: 1px; }
  .break-title { position: absolute; left: 0; width: 100%; top: 116px; text-align: center; font-size: 19px; font-weight: 700; letter-spacing: 1.5px; }
  .break-title em { font-style: italic; color: var(--cyan); }
  .closing-brand { position: absolute; left: 40px; top: 72px; display: flex; align-items: center; gap: 14px; font-size: 30px; font-weight: 600; letter-spacing: .5px; }
  .closing-brand .brand-dot { width: 26px; height: 26px; border-width: 4px; }
</style>
</head>
<body>

<!-- 1. Title slide -->
<section class="slide col-a row-1">
  <svg width="386" height="217" style="position:absolute;left:0;top:0" aria-hidden="true">
    <path d="M0 170 Q40 165 60 217" fill="none" stroke="#2a2a2b" stroke-width="1"/>
  </svg>
  <div class="cover-rule"></div>
  <div class="cover-brand"><span class="brand-dot"></span>Talon Microsystems</div>
  <h1 class="cover-title">BUSINESS<br><span class="accent">PRESENTATION</span></h1>
  <div class="cover-meta"><span>PRESENTER’S NAME</span><span class="divider"></span><span>DATE: 12-20-2024</span></div>
</section>

<!-- 2. Four-box content slide -->
<section class="slide col-b row-1">
  <div class="top-band"></div>
  <div class="title-tick" style="left:66px;top:10px"></div>
  <h2 class="slide-title" style="left:66px;top:28px">YOUR <span class="accent">CONTENT</span> SLIDE</h2>

  <div class="info-box" style="left:23px;top:68px"><span class="num">01</span><h3>CONTENT HEADER</h3>
    <p>Lorem ipsum dolor sit amet, consectetuer adipiscing elit. Aenean commodo ligula eget dolor.</p>
    <ul><li class="bullet"><span class="knob"></span>Lorem ipsum dolor sit amet, consectetuer adipiscing elit.</li><li class="bullet"><span class="knob"></span>Lorem ipsum dolor sit amet, consectetuer adipiscing elit.</li></ul></div>
  <div class="info-box" style="left:196px;top:68px"><span class="num">02</span><h3>CONTENT HEADER</h3>
    <p>Lorem ipsum dolor sit amet, consectetuer adipiscing elit. Aenean commodo ligula eget dolor.</p>
    <ul><li class="bullet"><span class="knob"></span>Lorem ipsum dolor sit amet, consectetuer adipiscing elit.</li><li class="bullet"><span class="knob"></span>Lorem ipsum dolor sit amet, consectetuer adipiscing elit.</li></ul></div>
  <div class="info-box" style="left:23px;top:123px"><span class="num">03</span><h3>CONTENT HEADER</h3>
    <p>Lorem ipsum dolor sit amet, consectetuer adipiscing elit. Aenean commodo ligula eget dolor.</p>
    <ul><li class="bullet"><span class="knob"></span>Lorem ipsum dolor sit amet, consectetuer adipiscing elit.</li><li class="bullet"><span class="knob"></span>Lorem ipsum dolor sit amet, consectetuer adipiscing elit.</li></ul></div>
  <div class="info-box" style="left:196px;top:123px"><span class="num">04</span><h3>CONTENT HEADER</h3>
    <p>Lorem ipsum dolor sit amet, consectetuer adipiscing elit. Aenean commodo ligula eget dolor.</p>
    <ul><li class="bullet"><span class="knob"></span>Lorem ipsum dolor sit amet, consectetuer adipiscing elit.</li><li class="bullet"><span class="knob"></span>Lorem ipsum dolor sit amet, consectetuer adipiscing elit.</li></ul></div>

  <footer class="footer"><span class="rule"></span><span class="corner left"></span><span class="corner right"></span>
    <div class="footer-brand"><span class="brand-dot"></span>Talon Microsystems</div>
    <span class="copyright">©Copyright 2023 Talon Microsystems.</span><span class="slide-num">SLIDE #</span></footer>
</section>

<!-- 3. Two-row content slide -->
<section class="slide col-a row-2">
  <div class="top-band"></div>
  <div class="title-tick" style="left:51px;top:23px"></div>
  <h2 class="slide-title" style="left:51px;top:30px">CONTENT <span class="accent">HEADER</span> SLIDE</h2>

  <span class="row-num" style="left:39px;top:76px">01</span>
  <p class="row-lead" style="top:65px">Lorem ipsum dolor sit amet, consectetuer adipiscing elit. Aenean commodo ligula eget dolor. Aenean massa.</p>
  <ul class="row-list" style="top:86px"><li class="bullet"><span class="knob"></span>Lorem ipsum dolor sit amet, consectetuer adipiscing elit.</li><li class="bullet"><span class="knob"></span>Lorem ipsum dolor sit amet, consectetuer adipiscing elit.</li></ul>
  <div class="row-divider" style="top:123px"></div>
  <span class="row-num" style="left:39px;top:142px">02</span>
  <p class="row-lead" style="top:132px">Lorem ipsum dolor sit amet, consectetuer adipiscing elit. Aenean commodo ligula eget dolor. Aenean massa.</p>
  <ul class="row-list" style="top:151px"><li class="bullet"><span class="knob"></span>Lorem ipsum dolor sit amet, consectetuer adipiscing elit.</li><li class="bullet"><span class="knob"></span>Lorem ipsum dolor sit amet, consectetuer adipiscing elit.</li></ul>

  <footer class="footer"><span class="rule"></span><span class="corner left"></span><span class="corner right"></span>
    <div class="footer-brand"><span class="brand-dot"></span>Talon Microsystems</div>
    <span class="copyright">©Copyright 2023 Talon Microsystems.</span><span class="slide-num">SLIDE #</span></footer>
</section>

<!-- 4. Two-column content slide -->
<section class="slide col-b row-2">
  <div class="top-band"></div>
  <div class="title-tick" style="left:51px;top:23px"></div>
  <h2 class="slide-title" style="left:51px;top:30px">CONTENT <span class="accent">HEADER</span> SLIDE</h2>

  <span class="col-num" style="left:31px">01</span>
  <p class="col-lead" style="left:67px">Lorem ipsum dolor sit amet, consectetuer adipiscing elit. Aenean commodo ligula eget dolor. Aenean massa.</p>
  <ul class="col-list" style="left:66px"><li><span class="bullet" style="white-space:nowrap"><span class="knob"></span></span><span>Lorem ipsum dolor sit amet, consectetuer adipiscing elit.</span></li><li><span class="bullet" style="white-space:nowrap"><span class="knob"></span></span><span>Lorem ipsum dolor sit amet, consectetuer adipiscing elit.</span></li></ul>
  <div class="col-divider"></div>
  <span class="col-num" style="left:207px">02</span>
  <p class="col-lead" style="left:243px">Lorem ipsum dolor sit amet, consectetuer adipiscing elit. Aenean commodo ligula eget dolor. Aenean massa.</p>
  <ul class="col-list" style="left:242px"><li><span class="bullet" style="white-space:nowrap"><span class="knob"></span></span><span>Lorem ipsum dolor sit amet, consectetuer adipiscing elit.</span></li><li><span class="bullet" style="white-space:nowrap"><span class="knob"></span></span><span>Lorem ipsum dolor sit amet, consectetuer adipiscing elit.</span></li></ul>

  <footer class="footer"><span class="rule"></span><span class="corner left"></span><span class="corner right"></span>
    <div class="footer-brand"><span class="brand-dot"></span>Talon Microsystems</div>
    <span class="copyright">©Copyright 2023 Talon Microsystems.</span><span class="slide-num">SLIDE #</span></footer>
</section>

<!-- 5. Four-column content slide -->
<section class="slide col-a row-3">
  <div class="top-band"></div>
  <div class="title-tick" style="left:51px;top:23px"></div>
  <h2 class="slide-title" style="left:51px;top:30px">CONTENT <span class="accent">HEADER</span> SLIDE</h2>

  <div class="quad" style="left:26px">
    <div class="head"><span class="num">01</span>
      <svg width="28" height="12" viewBox="0 0 28 12" fill="none" stroke="#fff" stroke-width=".8" aria-hidden="true"><circle cx="6" cy="4" r="2.5"/><circle cx="14" cy="4" r="2.5"/><circle cx="22" cy="4" r="2.5"/><path d="M1 11c0-3 2-4.5 5-4.5s5 1.5 5 4.5M9 11c0-3 2-4.5 5-4.5s5 1.5 5 4.5M17 11c0-3 2-4.5 5-4.5s5 1.5 5 4.5"/></svg></div>
    <h4>Subsection Title</h4>
    <p>Lorem ipsum dolor sit amet, consectetuer adipiscing elit. Aenean commodo ligula eget dolor. Aenean massa.</p>
    <ul><li class="bullet"><span class="knob"></span><span>Lorem ipsum dolor sit amet, consectetuer adipiscing elit.</span></li><li class="bullet"><span class="knob"></span><span>Lorem ipsum dolor sit amet, consectetuer adipiscing elit.</span></li></ul>
  </div>
  <div class="quad-divider" style="left:106px"></div>
  <div class="quad" style="left:114px">
    <div class="head"><span class="num">02</span>
      <svg width="14" height="14" viewBox="0 0 14 14" fill="none" stroke="#fff" stroke-width=".9" aria-hidden="true"><circle cx="7" cy="7" r="6"/><path d="M7 3.5V7l2.2 1.6"/></svg></div>
    <h4>Subsection Title</h4>
    <p>Lorem ipsum dolor sit amet, consectetuer adipiscing elit. Aenean commodo ligula eget dolor. Aenean massa.</p>
    <ul><li class="bullet"><span class="knob"></span><span>Lorem ipsum dolor sit amet, consectetuer adipiscing elit.</span></li><li class="bullet"><span class="knob"></span><span>Lorem ipsum dolor sit amet, consectetuer adipiscing elit.</span></li></ul>
  </div>
  <div class="quad-divider" style="left:195px"></div>
  <div class="quad" style="left:202px">
    <div class="head"><span class="num">03</span>
      <svg width="14" height="14" viewBox="0 0 14 14" fill="none" stroke="#fff" stroke-width=".9" aria-hidden="true"><path d="M3 11l2-4 5-5.5c1.5-.5 2.5-.5 3-.5 0 .5 0 1.5-.5 3L7 9z"/><circle cx="9.5" cy="4.5" r="1"/><path d="M2 13l2-2"/></svg></div>
    <h4>Subsection Title</h4>
    <p>Lorem ipsum dolor sit amet, consectetuer adipiscing elit. Aenean commodo ligula eget dolor. Aenean massa.</p>
    <ul><li class="bullet"><span class="knob"></span><span>Lorem ipsum dolor sit amet, consectetuer adipiscing elit.</span></li><li class="bullet"><span class="knob"></span><span>Lorem ipsum dolor sit amet, consectetuer adipiscing elit.</span></li></ul>
  </div>
  <div class="quad-divider" style="left:284px"></div>
  <div class="quad" style="left:290px">
    <div class="head"><span class="num">04</span>
      <svg width="17" height="14" viewBox="0 0 17 14" fill="none" stroke="#fff" stroke-width=".9" aria-hidden="true"><path d="M6 2h7a3 3 0 0 1 3 3v2a3 3 0 0 1-3 3h-1l1 3-4-3H6"/><path d="M1 6a3 3 0 0 1 3-3h4a3 3 0 0 1 3 3v1a3 3 0 0 1-3 3H5l-3 2 1-2.5A3 3 0 0 1 1 7z"/></svg></div>
    <h4>Subsection Title</h4>
    <p>Lorem ipsum dolor sit amet, consectetuer adipiscing elit. Aenean commodo ligula eget dolor. Aenean massa.</p>
    <ul><li class="bullet"><span class="knob"></span><span>Lorem ipsum dolor sit amet, consectetuer adipiscing elit.</span></li><li class="bullet"><span class="knob"></span><span>Lorem ipsum dolor sit amet, consectetuer adipiscing elit.</span></li></ul>
  </div>

  <footer class="footer"><span class="rule"></span><span class="corner left"></span><span class="corner right"></span>
    <div class="footer-brand"><span class="brand-dot"></span>Talon Microsystems</div>
    <span class="copyright">©Copyright 2023 Talon Microsystems.</span><span class="slide-num">SLIDE #</span></footer>
</section>

<!-- 6. Image slide -->
<section class="slide col-b row-3">
  <div class="top-band"></div>
  <div class="title-tick" style="left:40px;top:61px"></div>
  <h2 class="side-title">CONTENT<br><span class="accent">HEADER</span><br>SLIDE</h2>
  <div class="image-well" role="img" aria-label="Photo placeholder: a hand touching a glowing blue circuit-brain interface"><span>INSERT YOUR<br>IMAGE HERE</span></div>
  <footer class="footer"><span class="rule"></span><span class="corner left"></span><span class="corner right"></span>
    <div class="footer-brand"><span class="brand-dot"></span>Talon Microsystems</div>
    <span class="copyright">©Copyright 2023 Talon Microsystems.</span><span class="slide-num">SLIDE #</span></footer>
</section>

<!-- 7. Chart slide -->
<section class="slide col-a row-4">
  <div class="top-band reverse"></div>
  <div class="title-tick" style="left:51px;top:23px"></div>
  <h2 class="slide-title" style="left:51px;top:30px">CONTENT <span class="accent">HEADER</span> SLIDE</h2>
  <p class="chart-caption">YOUR CONTENT GRAPHS STYLE</p>
  <svg width="386" height="217" viewBox="0 0 386 217" style="position:absolute;left:0;top:0" font-family="Montserrat, sans-serif" font-size="5" font-weight="600" fill="#fff">
    <g stroke="#3a3a3c" stroke-width=".5">
      <path d="M36 86H219M36 99H219M36 111H219M36 124H219M36 136H219M36 149H219M36 161H219"/>
      <path d="M36 86V161M53 86V161M70 86V161M87 86V161M104 86V161M121 86V161M137 86V161M154 86V161M171 86V161M188 86V161M205 86V161M219 86V161"/>
    </g>
    <g text-anchor="end"><text x="32" y="88">70</text><text x="32" y="101">60</text><text x="32" y="113">50</text><text x="32" y="125">40</text><text x="32" y="138">30</text><text x="32" y="150">20</text><text x="32" y="163">10</text><text x="32" y="176">0</text></g>
    <g text-anchor="middle"><text x="50" y="176">2015</text><text x="68" y="176">2016</text><text x="85" y="176">2017</text><text x="101" y="176">2018</text><text x="118" y="176">2019</text><text x="136" y="176">2020</text><text x="153" y="176">2021</text><text x="170" y="176">2022</text><text x="186" y="176">2023</text><text x="203" y="176">2024</text></g>
    <polygon points="52,137 69,131 85,149 101,137 118,137 135,112 152,118 168,106 185,118 202,118 202,161 52,161" fill="#ffffff" fill-opacity=".07"/>
    <polyline points="52,137 69,131 85,149 101,137 118,137 135,112 152,118 168,106 185,118 202,118" fill="none" stroke="#6cc8e8" stroke-width="1"/>
    <g fill="#fff"><circle cx="52" cy="137" r="1.6"/><circle cx="69" cy="131" r="1.6"/><circle cx="85" cy="149" r="1.6"/><circle cx="101" cy="137" r="1.6"/><circle cx="118" cy="137" r="1.6"/><circle cx="135" cy="112" r="1.6"/><circle cx="152" cy="118" r="1.6"/><circle cx="168" cy="106" r="1.6"/><circle cx="185" cy="118" r="1.6"/><circle cx="202" cy="118" r="1.6"/></g>
    <g fill="#fff"><rect x="239" y="87" width="14" height="82"/><rect x="262" y="87" width="14" height="82"/><rect x="284" y="87" width="14" height="82"/><rect x="307" y="87" width="14" height="82"/><rect x="330" y="87" width="14" height="82"/><rect x="352" y="87" width="14" height="82"/></g>
    <g fill="#6cc8e8"><rect x="239" y="159" width="14" height="10"/><rect x="262" y="153" width="14" height="16"/><rect x="284" y="146" width="14" height="23"/><rect x="307" y="137" width="14" height="32"/><rect x="330" y="123" width="14" height="46"/><rect x="352" y="115" width="14" height="54"/></g>
    <g font-size="4" text-anchor="middle"><text x="246" y="166">15%</text><text x="269" y="163">25%</text><text x="291" y="160">35%</text><text x="314" y="155">55%</text><text x="337" y="149">65%</text><text x="359" y="143">75%</text></g>
    <g text-anchor="middle"><text x="246" y="176">2019</text><text x="269" y="176">2020</text><text x="291" y="176">2021</text><text x="314" y="176">2022</text><text x="337" y="176">2023</text><text x="359" y="176">2024</text></g>
  </svg>
  <footer class="footer"><span class="rule"></span><span class="corner left"></span><span class="corner right"></span>
    <div class="footer-brand"><span class="brand-dot"></span>Talon Microsystems</div>
    <span class="copyright">©Copyright 2023 Talon Microsystems.</span><span class="slide-num">SLIDE #</span></footer>
</section>

<!-- 8. Title-only slide -->
<section class="slide col-b row-4">
  <div class="top-band reverse"></div>
  <svg width="386" height="217" style="position:absolute;left:0;top:0" aria-hidden="true">
    <defs><linearGradient id="arc-a" x1="0" x2="1"><stop offset="0" stop-color="#0a4dff"/><stop offset="1" stop-color="#0f62ff"/></linearGradient></defs>
    <path d="M272 3 Q320 52 386 52 L386 34 Q336 34 298 3 Z" fill="url(#arc-a)"/>
    <path d="M0 118 Q45 140 67 192 L50 192 Q30 152 0 140 Z" fill="url(#arc-a)"/>
  </svg>
  <h2 class="center-title">YOUR <span class="accent">TITLE</span> SLIDE</h2>
  <footer class="footer"><span class="rule"></span><span class="corner left"></span><span class="corner right"></span>
    <div class="footer-brand"><span class="brand-dot"></span>Talon Microsystems</div>
    <span class="copyright">©Copyright 2023 Talon Microsystems.</span><span class="slide-num">SLIDE #</span></footer>
</section>

<!-- 9. Break slide -->
<section class="slide col-a row-5">
  <div class="top-band reverse"></div>
  <svg width="60" height="58" viewBox="0 0 60 58" style="position:absolute;left:162px;top:52px" fill="none" stroke="#fff" stroke-width="1.6" aria-hidden="true">
    <path d="M14 14c-3-3 3-5 0-8M24 14c-3-3 3-5 0-8M34 14c-3-3 3-5 0-8"/>
    <path d="M6 27h34v14a10 10 0 0 1-10 10h-14a10 10 0 0 1-10-10z"/>
    <path d="M40 31h5a5 5 0 0 1 0 10h-5"/>
    <rect x="18" y="32" width="10" height="10"/>
    <path d="M2 56h46"/>
  </svg>
  <h2 class="break-title">BREAK <em>SLIDE</em></h2>
  <footer class="footer"><span class="rule"></span><span class="corner left"></span><span class="corner right"></span>
    <div class="footer-brand"><span class="brand-dot"></span>Talon Microsystems</div>
    <span class="copyright">©Copyright 2023 Talon Microsystems.</span><span class="slide-num">SLIDE #</span></footer>
</section>

<!-- 10. Closing slide -->
<section class="slide col-b row-5">
  <div class="top-band reverse"></div>
  <svg width="386" height="217" style="position:absolute;left:0;top:0" aria-hidden="true">
    <path d="M228 3 Q280 62 386 58 L386 30 Q300 34 262 3 Z" fill="#0f5bff"/>
  </svg>
  <div class="closing-brand"><span class="brand-dot"></span>Talon Microsystems</div>
  <footer class="footer"><span class="rule"></span><span class="corner left"></span><span class="corner right"></span>
    <div class="footer-brand"><span class="brand-dot"></span>Talon Microsystems</div>
    <span class="copyright">©Copyright 2023 Talon Microsystems.</span><span class="slide-num">SLIDE #</span></footer>
</section>

</body>
</html>
```